Homemaking training schools needs a Business Card design

Designer, Hello!

No special requirements, good-looking enough.
--------------------------------------------------------------------------

Name: Marcus Dole
Chairman
Tel: 0574-71948263
Mobile: 13857420916
Email: kelvora@mailnest.example
Web: www.prt2019.example
Add: No.258, LanpingJie, BeiyuanQu, Ningbo, Zhejiang

LOGO
Ningbo PRT Homemaking Training School

Target Market(s)

pregnant women, mothers, infants, the elderly and families, including cleaning, cooking, nursing training.

Industry/Entity Type

Business

Contact Information for Business Card

Name: Marcus Dole
Chairman
Tel: 0574-71948263
Mobile: 13857420916
Email: kelvora@mailnest.example
Web: www.prt2019.example

LOGO

Font styles to use
Serif
Sans Serif
Decorative

Requirements
Nice to have
• Feels: clean, specifications, safety, comfort, warmth and happiness.

```html
<!DOCTYPE html>
<html lang="en">
<head>
<meta charset="utf-8">
<title>PingRuiTang Business Card</title>
<link rel="stylesheet" href="https://fonts.googleapis.com/css2?family=Open+Sans:wght@400;600;700&display=swap">
<style>
  :root {
    --stage: #000000;
    --card-light: #f3f3f3;
    --brand-blue: #1b72bb;
    --ink: #1f1f1f;
    --muted: #555555;
    --white: #ffffff;
  }
  * { margin: 0; padding: 0; box-sizing: border-box; }
  html, body { width: 1200px; height: 900px; overflow: hidden; background: var(--stage); }
  .canvas { position: relative; width: 1200px; height: 900px; font-family: "Open Sans", Arial, sans-serif; }

  .card { position: absolute; top: 200px; width: 310px; height: 502px; overflow: hidden; }
  .card--front { left: 265px; background: var(--card-light); border-radius: 55px 0 55px 0; }
  .card--back { left: 641px; background: var(--brand-blue); border-radius: 0 55px 0 55px; }

  .brand { position: absolute; left: 0; width: 100%; text-align: center; }
  .brand__name { font-weight: 600; letter-spacing: -0.5px; line-height: 1; }
  .brand__tagline { display: flex; align-items: center; justify-content: center; gap: 6px;
    font-size: 13px; line-height: 18px; margin-top: 5px; }
  .brand__tagline::before, .brand__tagline::after { content: ""; height: 1px; flex: 0 0 54px; background: currentColor; }

  .card--front .brand { top: 103px; }
  .card--front .brand__name { font-size: 33px; color: var(--brand-blue); }
  .card--front .brand__tagline { color: var(--muted); }

  .card--back .brand { top: 394px; }
  .card--back .brand__name { font-size: 32px; color: var(--white); }
  .card--back .brand__tagline { color: var(--white); }

  .person { position: absolute; left: 28px; top: 287px; }
  .person__name { font-size: 18px; font-weight: 700; color: var(--brand-blue); line-height: 20px; }
  .person__role { font-size: 13px; color: var(--ink); line-height: 16px; margin-top: 2px; }
  .address { font-size: 13.5px; color: var(--ink); line-height: 22px; margin-top: 13px; }
  .contacts { list-style: none; margin-top: 10px; }
  .contacts li { display: flex; align-items: center; gap: 6px; font-size: 13.5px; color: var(--ink); line-height: 21px; }
  .contacts svg { width: 10px; height: 10px; fill: var(--brand-blue); flex: none; }
</style>
</head>
<body>
<div class="canvas">
  <section class="card card--front">
    <div class="brand">
      <div class="brand__name">PingRuiTang</div>
      <div class="brand__tagline">Training &amp; Services</div>
    </div>
    <div class="person">
      <div class="person__name">Marcus Dole</div>
      <div class="person__role">Chairman</div>
      <p class="address">No.258, LanpingJie,<br>BeiyuanQu, Ningbo, Zhejiang</p>
      <ul class="contacts">
        <li><svg viewBox="0 0 10 10"><path d="M2 0.5 L3.8 2.6 L2.8 3.8 Q4 6 6.2 7.2 L7.4 6.2 L9.5 8 L8.2 9.5 Q3.5 9 0.5 1.8 Z"/></svg>0574-71948263</li>
        <li><svg viewBox="0 0 10 10"><path d="M2.5 0 H7.5 V10 H2.5 Z M3.4 1 V8 H6.6 V1 Z" fill-rule="evenodd"/></svg>13857420916</li>
        <li><svg viewBox="0 0 10 10"><path d="M0 2 H10 V8.5 H0 Z M0.8 2.6 L5 5.6 L9.2 2.6 V3.4 L5 6.4 L0.8 3.4 Z" fill-rule="evenodd"/></svg>kelvora@mailnest.example</li>
        <li><svg viewBox="0 0 10 10"><circle cx="5" cy="5" r="4.5"/></svg>www.prt2019.example</li>
      </ul>
    </div>
  </section>

  <section class="card card--back">
    <div class="brand">
      <div class="brand__name">PingRuiTang</div>
      <div class="brand__tagline">Training &amp; Services</div>
    </div>
  </section>
</div>
</body>
</html>
```